Ward Compass Business Card Design*

We need a business card design for our company Ward Compass. Our company is specialized in providing online consulting services regarding medical institutions, hospitals and doctors. We work with patients worldwide looking to choose between healthcare providers. We have a website you may use as a reference, where we list doctors and clinics worldwide. So we target Medical providers as well as patients worldwide.
Target Market(s)
Medical Providers and patients around the world
Industry/Entity Type
Medical
Contact Information for Business Card
Salwa Kettani
CEO
+90 612 348 2175
info@wardcompass.example
www.wardcompass.example
14 Annakhil 7 H.R.B. Rabat, Morocco
Requirements
Must have
- Company logo/name on one full side, personal info and smaller logo and company name on the other side.
Nice to have
- Smart and elegant design

```html
<!DOCTYPE html>
<html lang="en">
<head>
<meta charset="utf-8">
<title>Ward Compass – Business Card</title>
<link rel="stylesheet" href="https://fonts.googleapis.com/css2?family=Montserrat:wght@600&family=Poppins:wght@400;500&display=swap">
<style>
  :root {
    --bg: #2b2b2b;
    --navy: #163c6e;
    --grey: #7d7d7d;
    --text: #555555;
    --white: #ffffff;
    --rule: #9fb0c8;
  }
  * { box-sizing: border-box; margin: 0; padding: 0; }
  html, body { width: 1200px; height: 960px; overflow: hidden; }
  body { background: var(--bg); position: relative; font-family: "Poppins", sans-serif; }

  .card {
    position: absolute;
    width: 600px;
    height: 343px;
    box-shadow: 0 14px 30px rgba(0,0,0,.45);
  }

  /* Front side */
  .card--front {
    left: 110px; top: 80px;
    background: var(--navy);
    display: flex; align-items: center; justify-content: center; gap: 16px;
  }
  .brand-dot {
    width: 40px; height: 40px; border-radius: 50%;
    border: 6px solid var(--white);
  }
  .brand-name {
    font-family: "Montserrat", sans-serif;
    font-weight: 600;
    font-size: 30px;
    letter-spacing: 2px;
    color: var(--white);
  }

  /* Back side */
  .card--back {
    left: 490px; top: 530px;
    background: var(--white);
  }
  .back-brand {
    position: absolute; left: 56px; top: 104px; width: 160px;
    display: flex; flex-direction: column; align-items: center; gap: 12px;
  }
  .back-brand .brand-dot { width: 64px; height: 64px; border: 8px solid var(--navy); }
  .back-brand .brand-name { font-size: 15px; letter-spacing: 1.5px; color: var(--navy); }

  .divider {
    position: absolute; left: 238px; top: 84px;
    width: 1px; height: 132px; background: var(--rule);
  }
  .person { position: absolute; left: 264px; top: 84px; }
  .person__name { font-weight: 500; font-size: 24px; color: var(--navy); line-height: 1.1; }
  .person__role { font-size: 13px; color: var(--grey); margin: 4px 0 12px; }
  .contact { list-style: none; }
  .contact li {
    display: flex; align-items: center; gap: 9px;
    font-size: 13px; color: var(--text); line-height: 1.75;
  }
  .contact svg { width: 12px; height: 12px; fill: var(--navy); flex: none; }

  .address {
    position: absolute; left: 56px; bottom: 40px;
    display: flex; align-items: center; gap: 9px;
    font-size: 13px; color: var(--text);
  }
  .address svg { width: 13px; height: 15px; fill: var(--navy); }
</style>
</head>
<body>

<section class="card card--front" aria-label="Card front">
  <span class="brand-dot"></span>
  <span class="brand-name">WARD COMPASS</span>
</section>

<section class="card card--back" aria-label="Card back">
  <div class="back-brand">
    <span class="brand-dot"></span>
    <span class="brand-name">WARD COMPASS</span>
  </div>

  <div class="divider"></div>

  <div class="person">
    <p class="person__name">Salwa Kettani</p>
    <p class="person__role">CEO</p>
    <ul class="contact">
      <li>
        <svg viewBox="0 0 24 24"><path d="M6.6 10.8a15.1 15.1 0 0 0 6.6 6.6l2.2-2.2c.3-.3.7-.4 1-.2 1.1.4 2.3.6 3.6.6.6 0 1 .4 1 1V20c0 .6-.4 1-1 1A17 17 0 0 1 3 4c0-.6.4-1 1-1h3.5c.6 0 1 .4 1 1 0 1.3.2 2.5.6 3.6.1.3 0 .7-.2 1z"/></svg>
        +90 612 348 2175
      </li>
      <li>
        <svg viewBox="0 0 24 24"><path d="M2 5h20v14H2zm2 2v.5l8 5 8-5V7l-8 5z"/></svg>
        info@wardcompass.example
      </li>
      <li>
        <svg viewBox="0 0 24 24"><circle cx="12" cy="12" r="10"/></svg>
        www.wardcompass.example
      </li>
    </ul>
  </div>

  <p class="address">
    <svg viewBox="0 0 24 28"><path d="M12 0a10 10 0 0 0-10 10c0 7.5 10 18 10 18s10-10.5 10-18A10 10 0 0 0 12 0zm0 14a4 4 0 1 1 0-8 4 4 0 0 1 0 8z"/></svg>
    14 Annakhil 7 H.R.B. Rabat, Morocco
  </p>
</section>

</body>
</html>
```